Simple Logo Design for Semi-Clear Plastic Frosted Card stock

Create a business card on frosted plastic. compliment existing logo elements with a tree trunk, roots, or seed at the lower half and the full logo both on the front.

Contact information will go on a solid portion of the back of this design since this card stock is semi-transparent.

It is important to consider this plastic card stock medium in your design. I found helpful tips and guides listed at vellaprint-sample.net: be careful to understand ink printed on plastic cards cannot have too much of a consistent print area or risks peeling and fine lines can easily scratch off.
Updates

2" x 3.5" 20PT Clear Plastic Business cards with Round corners Please get info or templates here: https://www.vellaprint-sample.net/product-detail/2-x-35-20pt-clear-plastic-business-cards-with-round-corners

Target Market(s)

Not for profit- religion

Industry/Entity Type

Business

Must include complementary elements to the existing logo

Font styles to use
Decorative

Colors
000000

Requirements
Must have
• Elements of community, nature and oneness. Such as: seed, roots, tree trunk, etc.
• Three lines of space on the back for Name, Title, Phone Number.
Nice to have
• I like a light use of decorative elements
Should not have
• No eyes, from faces or animals.

```html
<!DOCTYPE html>
<html lang="en">
<head>
<meta charset="utf-8">
<title>Steadfast Grove – Business Cards</title>
<link href="https://fonts.googleapis.com/css2?family=Source+Sans+3:wght@400;600&display=swap" rel="stylesheet">
<style>
  :root {
    --page: #e9ecec;
    --frost-top: #5f9491;
    --frost-bottom: #a8cbca;
    --ink: #000000;
    --brand-teal: #2e807b;
    --leaf-green: #5aa83c;
    --white: #ffffff;
    --tagline-grey: #8a9493;
  }
  html, body {
    margin: 0;
    width: 1200px;
    height: 900px;
    overflow: hidden;
    background: var(--page);
    font-family: "Source Sans 3", "Helvetica Neue", Arial, sans-serif;
  }
  .canvas { position: relative; width: 1200px; height: 900px; }

  .card {
    position: absolute;
    overflow: hidden;
    background: linear-gradient(160deg, var(--frost-top), var(--frost-bottom));
    box-shadow: 0 2px 8px rgba(0,0,0,.15);
  }
  .card--front { left: 240px; top: 62px; width: 552px; height: 342px; }
  .card--back  { left: 458px; top: 518px; width: 558px; height: 342px; }

  .card__art { position: absolute; inset: 0; width: 100%; height: 100%; }

  .brand,
  .tagline {
    position: absolute;
    left: 0;
    right: 0;
    margin: 0;
    text-align: center;
    white-space: nowrap;
    line-height: 1;
  }
  .brand { color: var(--brand-teal); font-weight: 400; }
  .tagline { text-transform: uppercase; }

  .card--front .brand { top: 187px; font-size: 32px; letter-spacing: 1px; }
  .card--front .tagline { top: 224px; font-size: 11.5px; letter-spacing: 1px; color: var(--white); }

  .contact__name {
    position: absolute; left: 76px; top: 262px; margin: 0;
    font-size: 22px; font-weight: 600; color: var(--leaf-green); line-height: 1.1;
  }
  .contact__title {
    position: absolute; left: 97px; top: 293px; margin: 0;
    font-size: 16px; color: var(--white); line-height: 1.1;
  }
  .contact__phone {
    position: absolute; left: 281px; top: 277px;
    display: flex; align-items: center; gap: 7px;
    font-size: 18px; color: var(--white); line-height: 1.1;
  }

  .card--back .brand { top: 255px; font-size: 57px; letter-spacing: 2px; }
  .card--back .tagline { top: 309px; font-size: 19px; letter-spacing: 2.5px; color: var(--tagline-grey); }
</style>
</head>
<body>
<main class="canvas">

  <section class="card card--front" aria-label="Contact side of business card">
    <svg class="card__art" viewBox="0 0 552 342" aria-hidden="true">
      <rect x="0" y="234" width="552" height="108" fill="var(--ink)"/>
      <path d="M97 234 A178 178 0 0 1 453 234 Z" fill="var(--ink)"/>
      <circle cx="275" cy="120" r="54" fill="var(--brand-teal)"/>
    </svg>
    <p class="brand">STEADFAST GROVE</p>
    <p class="tagline">Learning, Fellowship &amp; Calm</p>
    <p class="contact__name">Daniel Hale</p>
    <p class="contact__title">Managing Director</p>
    <div class="contact__phone">
      <svg width="15" height="15" viewBox="0 0 24 24" aria-hidden="true">
        <path fill="var(--leaf-green)" d="M6.6 10.8a15.1 15.1 0 0 0 6.6 6.6l2.2-2.2c.3-.3.7-.4 1-.2 1.1.4 2.3.6 3.6.6.6 0 1 .4 1 1V20c0 .6-.4 1-1 1A17 17 0 0 1 3 4c0-.6.4-1 1-1h3.5c.6 0 1 .4 1 1 0 1.3.2 2.5.6 3.6.1.3 0 .7-.2 1z"/>
      </svg>
      <span>044-987 654 321</span>
    </div>
  </section>

  <section class="card card--back" aria-label="Brand side of business card">
    <svg class="card__art" viewBox="0 0 558 342" aria-hidden="true">
      <rect x="0" y="234" width="558" height="108" fill="var(--ink)"/>
      <path d="M101 234 A178 178 0 0 1 457 234 Z" fill="var(--ink)"/>
      <circle cx="279" cy="150" r="70" fill="var(--brand-teal)"/>
    </svg>
    <p class="brand">STEADFAST GROVE</p>
    <p class="tagline">Learning, Fellowship &amp; Calm</p>
  </section>

</main>
</body>
</html>
```